Stylish Business Cards Wanted

- DOUBLE SIDED Design Required -

High end, edgy cards for a corporate and personal stylist. Must include logo,
Name: Belinda Harwick
Title: Director and Stylist
telephone : +61 8 7142 5809
email: belinda@theloombriefing.example
website: theloombriefing.example
Tag: Corporate Workwear & Uniform Specialist | Personal Stylist
Would like nice icons for telephone, email, website

Target Market(s)

Businesses wanting stylish uniforms, people wanting stylish wardrobes

Industry/Entity Type

Corporate Workwear Stylist

Contact Information for Business Card

I would like black, white and gold foiling incorporated in the design - possibly a touch of the other colours on my branding guide attached Name: Belinda Harwick Title: Director and Stylist telephone : +61 8 7142 5809 email: belinda@theloombriefing.example website: theloombriefing.example Tag: Corporate Workwear & Uniform Specialist | Personal Stylist Would like nice icons for telephone, email, website

Font styles to use
Other font styles liked:
• Raleway

Colors

Designer to choose colors to be used in the design.

Requirements
Must have
• Gold foil accents

```html
<!DOCTYPE html>
<html lang="en">
<head>
<meta charset="utf-8">
<title>The Loom Briefing – Business Card</title>
<link href="https://fonts.googleapis.com/css2?family=Raleway:wght@400;600;700&family=Courgette&display=swap" rel="stylesheet">
<style>
  :root {
    --backdrop: #2b2b2d;
    --paper: #ffffff;
    --navy: #141d33;
    --gold: #e2b23e;
    --gold-deep: #c9982a;
    --ink: #17203a;
  }
  * { margin: 0; padding: 0; box-sizing: border-box; }
  html, body { width: 799px; height: 1200px; overflow: hidden; }
  body {
    background: var(--backdrop);
    font-family: "Raleway", sans-serif;
    position: relative;
  }
  .card {
    position: absolute;
    left: 50px;
    width: 700px;
    height: 400px;
    border-radius: 28px;
    background: var(--paper);
    overflow: hidden;
    box-shadow: 0 10px 30px rgba(0,0,0,.45);
  }
  .card--front { top: 90px; }
  .card--back { top: 700px; }

  .front-wordmark {
    position: absolute;
    inset: 0;
    display: flex;
    align-items: center;
    justify-content: center;
    gap: 18px;
  }
  .front-wordmark .mark-dot {
    width: 26px; height: 26px; border-radius: 50%;
    background: var(--gold);
  }
  .front-wordmark .mark-name {
    font-family: "Raleway", sans-serif;
    font-weight: 700;
    font-size: 54px;
    color: var(--gold);
    letter-spacing: 1px;
  }

  .back-shapes { position: absolute; inset: 0; }

  .back-wordmark {
    position: absolute;
    left: 30px;
    top: 120px;
    width: 220px;
    text-align: center;
    font-family: "Raleway", sans-serif;
    font-weight: 700;
    font-size: 34px;
    line-height: 1.15;
    color: var(--paper);
  }

  .contact {
    position: absolute;
    left: 335px;
    top: 78px;
    color: var(--ink);
  }
  .contact__name {
    font-family: "Courgette", cursive;
    font-size: 34px;
    color: var(--gold);
    line-height: 1.1;
  }
  .contact__title {
    font-size: 17px;
    font-weight: 600;
    margin: 4px 0 14px;
  }
  .contact__list { list-style: none; }
  .contact__item {
    display: flex;
    align-items: center;
    gap: 12px;
    font-size: 18px;
    line-height: 30px;
  }
  .contact__item svg { width: 18px; height: 18px; flex: none; }

  .tagline {
    position: absolute;
    left: 30px;
    right: 30px;
    top: 312px;
    display: flex;
    justify-content: space-between;
    font-family: "Courgette", cursive;
    font-size: 18px;
    color: var(--ink);
  }
</style>
</head>
<body>

<section class="card card--front" aria-label="Card front">
  <div class="front-wordmark">
    <span class="mark-dot"></span>
    <span class="mark-name">The Loom Briefing</span>
  </div>
</section>

<section class="card card--back" aria-label="Card back">
  <svg class="back-shapes" viewBox="0 0 700 400" width="700" height="400" aria-hidden="true">
    <path d="M0 0 H330 C300 150 260 250 90 300 H0 Z" fill="var(--gold)"/>
    <path d="M0 0 H305 C280 140 235 240 40 300 H0 Z" fill="var(--navy)"/>
    <rect x="0" y="300" width="700" height="48" fill="var(--gold)"/>
  </svg>

  <div class="back-wordmark">The Loom<br>Briefing</div>

  <div class="contact">
    <div class="contact__name">Belinda Harwick</div>
    <div class="contact__title">Director and Stylist</div>
    <ul class="contact__list">
      <li class="contact__item">
        <svg viewBox="0 0 24 24" aria-hidden="true"><circle cx="12" cy="12" r="10.5" fill="none" stroke="var(--gold)" stroke-width="1.6"/><path d="M8.5 7.5c.5-.6 1.3-.6 1.7 0l.9 1.5c.3.5.2 1-.2 1.4l-.6.5c.6 1.3 1.6 2.3 2.9 2.9l.5-.6c.4-.4.9-.5 1.4-.2l1.5.9c.6.4.6 1.2 0 1.7-1.3 1.2-3 1-5-.6-1.7-1.4-3-3-3.6-4.5-.5-1.2-.4-2.2.5-3z" fill="var(--gold)"/></svg>
        +61 8 7142 5809
      </li>
      <li class="contact__item">
        <svg viewBox="0 0 24 24" aria-hidden="true"><rect x="2.5" y="5.5" width="19" height="13" rx="1.5" fill="none" stroke="var(--gold)" stroke-width="1.8"/><path d="M3 6.5l9 6.5 9-6.5" fill="none" stroke="var(--gold)" stroke-width="1.8"/></svg>
        belinda@theloombriefing.example
      </li>
      <li class="contact__item">
        <svg viewBox="0 0 24 24" aria-hidden="true"><g fill="none" stroke="var(--gold)" stroke-width="1.6"><circle cx="12" cy="12" r="9.5"/><ellipse cx="12" cy="12" rx="4" ry="9.5"/><path d="M2.5 12h19M4 7h16M4 17h16"/></g></svg>
        www.theloombriefing.example
      </li>
    </ul>
  </div>

  <div class="tagline">
    <span>Corporate Workwear &amp; Uniform Specialist</span>
    <span>Personal Stylist</span>
  </div>
</section>

</body>
</html>
```